Business Cards Needed for Innovative Healthcare Marketing Company

We are a marketing company focused on healthcare. Our company is all about rebranding yourself renewing your image and generating results. The phoenix stands for "reborn" or "rising" which we provide new brands for our clients we take their old brands and renew it with creativity and innovation. I am looking for a business card with color dimension. I have attached an example of a card I think has the look and feel of what I am trying to accomplish. I like that the card example has black and grey font colors, I like the font placement and the small logo, I really like the use of the colors on the right those are the colors of my logo. My logo is phoenix so maybe incorporating flames similar to that design. I would like the back a solid color maybe red with an opaque version of the logo and website. As a marketing company I am always open to creative liberty!

Target Market(s)

Doctors and business professionals.

Industry/Entity Type

Marketing

Contact Information for Business Card

Valcorne Health Care Marketing
Marla Tenwick- CEO
#(512)638-2974
email-marla@valcorne.com
website- valcorne.com

Font styles to use
Sans Serif

Colors
ec1f27
f37122
ffc214
fbed22
fbf289
f04a50

Requirements
Must have
• The logo and required information
Nice to have
• icons by the information
Should not have
• child like font

```html
<!DOCTYPE html>
<html lang="en">
<head>
<meta charset="utf-8">
<title>Valcorne Health Care Marketing – Business Card</title>
<link rel="stylesheet" href="https://fonts.googleapis.com/css2?family=Open+Sans:wght@300;400;700&display=swap">
<style>
  :root {
    --stage: #232323;
    --card-white: #ffffff;
    --brand-red: #a8232a;
    --brand-orange: #f0901e;
    --deep-red: #a3201f;
    --glow-orange: #f3952a;
    --text-grey: #4a4a4a;
    --white: #ffffff;
  }
  * { margin: 0; padding: 0; box-sizing: border-box; }
  html, body {
    width: 1200px;
    height: 987px;
    overflow: hidden;
  }
  body {
    position: relative;
    background: var(--stage);
    font-family: "Open Sans", Arial, sans-serif;
  }
  .card {
    position: absolute;
    left: 293px;
    width: 615px;
    height: 352px;
    box-shadow: 0 4px 10px rgba(0,0,0,0.5);
  }
  .card-front {
    top: 125px;
    background: var(--card-white);
  }
  .card-back {
    top: 511px;
    background: radial-gradient(ellipse 62% 78% at 50% 55%, var(--glow-orange) 0%, #d8641f 55%, var(--deep-red) 100%);
  }

  /* Front: identity */
  .person-name {
    position: absolute;
    right: 49px;
    top: 53px;
    font-size: 23px;
    font-weight: 700;
    color: var(--brand-red);
    letter-spacing: 0.2px;
  }
  .person-title {
    position: absolute;
    right: 49px;
    top: 84px;
    font-size: 17px;
    font-weight: 400;
    color: var(--brand-orange);
  }

  /* Front: contact list */
  .contact-list {
    position: absolute;
    right: 51px;
    top: 117px;
    list-style: none;
  }
  .contact-item {
    display: flex;
    align-items: center;
    justify-content: flex-end;
    height: 25px;
    font-size: 16px;
    color: var(--text-grey);
  }
  .contact-icon {
    width: 19px;
    height: 19px;
    margin-left: 9px;
    flex: none;
  }

  /* Front: wordmark */
  .wordmark-front {
    position: absolute;
    right: 50px;
    top: 208px;
    display: flex;
    align-items: center;
    gap: 14px;
  }
  .wordmark-dot {
    width: 58px;
    height: 58px;
    border-radius: 50%;
    background: var(--brand-orange);
    flex: none;
  }
  .wordmark-text {
    font-weight: 300;
    color: var(--brand-red);
    line-height: 1.1;
  }
  .wordmark-text .brand-name { display: block; font-size: 40px; letter-spacing: 1px; }
  .wordmark-text .brand-line { display: block; font-size: 14px; letter-spacing: 0.8px; }

  /* Back: wordmark */
  .wordmark-back {
    position: absolute;
    left: 0;
    right: 0;
    top: 92px;
    display: flex;
    flex-direction: column;
    align-items: center;
    gap: 16px;
  }
  .wordmark-back .wordmark-dot {
    width: 74px;
    height: 74px;
    background: transparent;
    border: 3px solid var(--white);
  }
  .wordmark-back .wordmark-text {
    color: var(--white);
    text-align: center;
  }
  .wordmark-back .brand-name { font-size: 40px; }
  .wordmark-back .brand-line { font-size: 14px; }
</style>
</head>
<body>

  <section class="card card-front" aria-label="Business card front">
    <h1 class="person-name">MARLA TENWICK</h1>
    <p class="person-title">CEO</p>

    <ul class="contact-list">
      <li class="contact-item">
        <span>(512)638-2974</span>
        <svg class="contact-icon" viewBox="0 0 20 20" aria-hidden="true">
          <circle cx="10" cy="10" r="10" fill="var(--brand-red)"/>
          <path d="M7 5.2l1.6 2.4-1 1.1c.6 1.3 1.6 2.3 2.8 2.9l1.1-1 2.4 1.6-.8 1.8c-3.6-.3-6.6-3.3-6.9-6.9z" fill="#fff"/>
        </svg>
      </li>
      <li class="contact-item">
        <span>marla@valcorne.com</span>
        <svg class="contact-icon" viewBox="0 0 20 20" aria-hidden="true">
          <circle cx="10" cy="10" r="10" fill="var(--brand-red)"/>
          <rect x="5" y="6.5" width="10" height="7" fill="#fff"/>
          <path d="M5 6.5l5 4 5-4" fill="none" stroke="var(--brand-red)" stroke-width="1.2"/>
        </svg>
      </li>
      <li class="contact-item">
        <span>www.valcorne.com</span>
        <svg class="contact-icon" viewBox="0 0 20 20" aria-hidden="true">
          <circle cx="10" cy="10" r="10" fill="var(--brand-red)"/>
          <circle cx="10" cy="10" r="5" fill="none" stroke="#fff" stroke-width="1.4"/>
          <path d="M5 10h10M10 5c-2 2.8-2 7.2 0 10M10 5c2 2.8 2 7.2 0 10" fill="none" stroke="#fff" stroke-width="1"/>
        </svg>
      </li>
    </ul>

    <div class="wordmark-front">
      <span class="wordmark-dot" aria-hidden="true"></span>
      <p class="wordmark-text">
        <span class="brand-name">VALCORNE</span>
        <span class="brand-line">HEALTH CARE MARKETING</span>
      </p>
    </div>
  </section>

  <section class="card card-back" aria-label="Business card back">
    <div class="wordmark-back">
      <span class="wordmark-dot" aria-hidden="true"></span>
      <p class="wordmark-text">
        <span class="brand-name">VALCORNE</span>
        <span class="brand-line">HEALTH CARE MARKETING</span>
      </p>
    </div>
  </section>

</body>
</html>
```